IT Services Company Needs Corporate PPT Template

This is urgent (need a fast turn around). We need a corporate PPT template deck (NOTE: Deck should be in 4:3 ratio) for our IT Services firm that is clean but slick and modern. We tend to lean more towards the flat design look. I'm attaching a zip file which includes our Corporate Branding Guide (which is in progress), color scheme, A PPT deck as inspiration (our logo is on the last slide), our font (LATO). Our newly launched website is located at: http://www.veranthix.com.

As an example of a deck we like see: http://slidemorrow.net/item/clean-multipurpose-business-presentation-template/5318206?WT.ac=category_thumb&WT.seg_1=category_thumb&WT.z_author=PixelHarbor
Although we don't want "this" deck - it gives an idea of style.

I'm also attaching a copy of our corporate deck as it is now to give you an idea of the type of content that would appear on various slides. We definitely want the following slides (at least) within the template:

Title Slide
Blank Slide
2 Column - with bullets
2 Column - no bullets
Single Column - no bullets
Single Column - with bullets
Various Charts and Tables (see example deck)
Meet the Team
Offering Slide
Customer Showcase
Timeline
Case Study
Contact US

Note: Being awarded this job will lead to a second job of creating our corporate deck.

Target Market(s)

CIO, CEO, Technology Officers, Sales People, Marketing, IT heads and staff, Customers, Prospective customers

Industry/Entity Type

Business

Requirements
Must have
• See description and attached files

```html
<!DOCTYPE html>
<html lang="en">
<head>
<meta charset="utf-8">
<title>Meet the Team – Veranthix</title>
<link href="https://fonts.googleapis.com/css2?family=Lato:wght@400;700;900&display=swap" rel="stylesheet">
<style>
  :root {
    --header-dark: #0b4f78;
    --header-mid: #13689a;
    --accent-light: #7fcbe6;
    --subtitle: #5bbcd6;
    --card-blue: #1a6ea3;
    --body-text: #454545;
    --footer-top: #f3f3f3;
    --footer-bottom: #e2e2e2;
    --presenter-blue: #2b8fd1;
    --brand-navy: #173f73;
    --photo-light: #4f86bf;
    --photo-dark: #1d4a80;
  }
  * { margin: 0; padding: 0; box-sizing: border-box; }
  html, body { width: 1200px; height: 900px; overflow: hidden; background: #ffffff; }
  body { font-family: "Lato", Arial, sans-serif; }
  .slide {
    position: relative; width: 1200px; height: 900px; overflow: hidden;
    background: radial-gradient(ellipse at 85% 40%, #eef1f4 0%, #ffffff 60%);
  }
  .slide-header {
    position: absolute; left: 0; top: 0; width: 100%; height: 99px;
    background: linear-gradient(90deg, var(--header-dark) 0%, var(--header-mid) 55%, var(--header-dark) 100%);
  }
  .slide-title {
    position: absolute; left: 33px; top: 24px;
    font-size: 39px; font-weight: 700; color: #ffffff; letter-spacing: -0.3px;
  }
  .slide-title .highlight { color: var(--accent-light); }
  .slide-subtitle {
    position: absolute; left: 34px; top: 136px;
    font-size: 27px; font-weight: 700; color: var(--subtitle);
  }
  .team-member { position: absolute; top: 214px; width: 220px; text-align: center; }
  .team-member:nth-of-type(1) { left: 68px; }
  .team-member:nth-of-type(2) { left: 340px; }
  .team-member:nth-of-type(3) { left: 610px; }
  .team-member:nth-of-type(4) { left: 882px; }
  .member-photo {
    width: 190px; height: 190px; margin: 0 auto; border-radius: 50%;
    background: radial-gradient(circle at 50% 35%, var(--photo-light) 0%, var(--photo-dark) 100%);
  }
  .member-label {
    position: relative; margin: 30px auto 0; width: 219px; height: 78px;
    background: var(--card-blue); color: #ffffff; padding-top: 10px;
  }
  .member-label svg { position: absolute; left: 50%; top: -14px; margin-left: -16px; }
  .member-name { font-size: 24px; font-weight: 700; line-height: 1.2; }
  .member-role { font-size: 20px; font-weight: 400; line-height: 1.3; }
  .member-bio {
    margin: 12px auto 0; width: 215px;
    font-size: 19.5px; line-height: 27px; color: var(--body-text);
  }
  .slide-footer {
    position: absolute; left: 0; bottom: 0; width: 100%; height: 82px;
    background: linear-gradient(180deg, var(--footer-top), var(--footer-bottom));
    box-shadow: 0 -2px 6px rgba(0,0,0,0.12);
  }
  .brand-name {
    position: absolute; left: 24px; top: 20px;
    font-size: 38px; font-weight: 900; color: var(--brand-navy); letter-spacing: 0.5px;
  }
  .presenter {
    position: absolute; right: 18px; top: 28px;
    font-size: 18px; color: var(--presenter-blue);
  }
  .presenter strong { font-size: 22px; font-weight: 700; margin-left: 4px; }
</style>
</head>
<body>
<div class="slide">
  <header class="slide-header">
    <h1 class="slide-title">Meet the <span class="highlight">Team</span></h1>
  </header>
  <h2 class="slide-subtitle">Team Slide text here</h2>

  <section class="team-member">
    <div class="member-photo" role="img" aria-label="Portrait photo of team member"></div>
    <div class="member-label">
      <svg width="32" height="15" viewBox="0 0 32 15"><polygon points="0,15 16,0 32,15" fill="#1a6ea3"/></svg>
      <div class="member-name">Evan Marlow</div>
      <div class="member-role">Solution Director</div>
    </div>
    <p class="member-bio">consectetur adipiscing elit. Cras ipsum leo, ves&shy;tibulum non orci id, vehicula convallis sem consectetur adipiscing elit. Cras ipsum leo, ves&shy;tibulum non orci id, vehicula convallis sem</p>
  </section>

  <section class="team-member">
    <div class="member-photo" role="img" aria-label="Portrait photo of team member"></div>
    <div class="member-label">
      <svg width="32" height="15" viewBox="0 0 32 15"><polygon points="0,15 16,0 32,15" fill="#1a6ea3"/></svg>
      <div class="member-name">Evan Marlow</div>
      <div class="member-role">Solution Director</div>
    </div>
    <p class="member-bio">consectetur adipiscing elit. Cras ipsum leo, ves&shy;tibulum non orci id, vehicula convallis sem consectetur adipiscing elit. Cras ipsum leo, ves&shy;tibulum non orci id, vehicula convallis sem</p>
  </section>

  <section class="team-member">
    <div class="member-photo" role="img" aria-label="Portrait photo of team member"></div>
    <div class="member-label">
      <svg width="32" height="15" viewBox="0 0 32 15"><polygon points="0,15 16,0 32,15" fill="#1a6ea3"/></svg>
      <div class="member-name">Evan Marlow</div>
      <div class="member-role">Solution Director</div>
    </div>
    <p class="member-bio">consectetur adipiscing elit. Cras ipsum leo, ves&shy;tibulum non orci id, vehicula convallis sem consectetur adipiscing elit. Cras ipsum leo, ves&shy;tibulum non orci id, vehicula convallis sem</p>
  </section>

  <section class="team-member">
    <div class="member-photo" role="img" aria-label="Portrait photo of team member"></div>
    <div class="member-label">
      <svg width="32" height="15" viewBox="0 0 32 15"><polygon points="0,15 16,0 32,15" fill="#1a6ea3"/></svg>
      <div class="member-name">Evan Marlow</div>
      <div class="member-role">Solution Director</div>
    </div>
    <p class="member-bio">consectetur adipiscing elit. Cras ipsum leo, ves&shy;tibulum non orci id, vehicula convallis sem consectetur adipiscing elit. Cras ipsum leo, ves&shy;tibulum non orci id, vehicula convallis sem</p>
  </section>

  <footer class="slide-footer">
    <div class="brand-name">Veranthix</div>
    <div class="presenter">Persentator Name &nbsp;:<strong>Lena Morvick</strong></div>
  </footer>
</div>
</body>
</html>
```